I need a SEO-friendly Wordpress website (making sure to style H1, H2, H3, etc correctly) for a Hawaii-based law firm called Meridian Crest Legal Group. Comparable websites include https://brvlaw.example/ and https://www.lomrit.example/ for design reference. The current copy on the TarnAdvocate.example website can be used.

```html
<!DOCTYPE html>
<html lang="en">
<head>
<meta charset="utf-8">
<title>Meridian Crest Legal Group</title>
<link href="https://fonts.googleapis.com/css2?family=Tinos:wght@400;700&family=Nunito+Sans:wght@300;400;600&display=swap" rel="stylesheet">
<style>
:root{
  --accent:#b8641a;
  --ink:#222;
  --muted:#6f6f6f;
  --rule:#d9d9d9;
  --dark:#141414;
  --white:#fff;
}
*{box-sizing:border-box;margin:0;padding:0}
html,body{width:1200px;height:3448px;overflow:hidden;background:var(--white)}
body{position:relative;font-family:"Nunito Sans",Arial,sans-serif;color:var(--ink)}
.serif{font-family:"Tinos","Times New Roman",serif}
.abs{position:absolute}
.hero{left:0;top:0;width:1200px;height:645px;background:linear-gradient(100deg,#1b1b1b 0%,#2a2a2a 45%,#3a3a3a 70%,#222 100%)}
.brand{left:79px;top:30px;font-family:"Tinos",serif;font-weight:700;font-size:25px;color:var(--white)}
.nav{right:78px;top:26px;display:flex;gap:26px;list-style:none}
.nav li{font-size:13px;color:#e6e6e6;padding-top:10px;letter-spacing:.2px}
.nav li.current{color:var(--accent);border-top:1px solid var(--accent)}
.hero-title{left:79px;top:302px;width:600px;font-family:"Tinos",serif;font-weight:700;font-size:51px;line-height:63px;color:var(--white)}
.about{left:77px;top:562px;width:1046px;height:511px;border:2px solid var(--accent)}
.label{font-size:15px;color:var(--accent);letter-spacing:.3px;text-transform:uppercase}
.about-label{left:210px;top:728px}
.about h2{position:absolute;left:133px;top:206px;font-weight:400;font-size:18px;color:var(--ink);font-family:"Nunito Sans",sans-serif}
.about p{position:absolute;left:133px;width:740px;font-size:13px;line-height:25px;color:var(--muted)}
.read-more{position:absolute;left:133px;top:406px;font-size:15px;color:var(--ink);display:flex;align-items:center;gap:14px}
.read-more span{text-decoration:underline}
.city{left:0;top:1155px;width:1200px;height:396px;background:linear-gradient(160deg,#3c3c3c 0%,#6e6e6e 40%,#8a8a8a 60%,#4a4a4a 100%)}
.practice-label{left:79px;top:1632px}
.practice{left:79px;top:1697px;width:1046px}
.row{position:relative;border-top:1px solid var(--rule)}
.row h3{position:absolute;left:0;top:60px;font-family:"Tinos",serif;font-weight:400;font-size:30px;color:var(--ink)}
.row p{position:absolute;left:341px;top:62px;width:705px;font-size:13px;line-height:25px;color:var(--muted)}
.row.last{border-bottom:1px solid var(--rule)}
.testimonials{left:0;top:2478px;width:1200px;height:478px;background:var(--dark)}
.testimonials .label{position:absolute;left:79px;top:101px}
.quote{position:absolute;left:79px;top:162px;width:1060px;font-family:"Tinos",serif;font-size:30px;line-height:42px;color:var(--white)}
.cite{position:absolute;left:79px;top:320px;font-size:16px;color:var(--white)}
.dots{position:absolute;left:570px;top:405px}
.contact-label{left:79px;top:3038px}
.contact-box{left:77px;top:3113px;width:1046px;height:208px;border:1px solid var(--rule);display:flex}
.col{border-right:1px solid var(--rule);padding:48px 0 0 22px}
.col:last-child{border-right:none}
.col h3{font-family:"Tinos",serif;font-weight:400;font-size:20px;color:var(--ink);margin-bottom:16px}
.col p{font-size:13px;line-height:25px;color:var(--muted);margin-bottom:15px}
.col p.tight{margin-bottom:0}
.footer{left:0;top:3380px;width:1200px;text-align:center;font-size:13px;color:var(--accent)}
</style>
</head>
<body>
<header>
  <div class="abs hero" role="img" aria-label="Dark monochrome photo of a lawyer at a desk with a statue of Lady Justice"></div>
  <div class="abs brand">Meridian Crest Legal Group</div>
  <ul class="abs nav">
    <li class="current">HOME</li><li>PRACTICE AREAS</li><li>ATTORNEYS</li><li>BLOG</li><li>CONTACT US</li>
  </ul>
  <h1 class="abs hero-title">Dedicated to making sure you receive the care and attention you need.</h1>
</header>

<section class="abs about">
  <h2>Lawyers Serving the Big Island and Neighboring Islands</h2>
  <p style="top:248px">The experienced attorneys in the Meridian Crest Legal Group's Kailua Kona, Hawaii office provide clients with a wide range of litigation expertise, including legal claims involving divorce &amp; family, personal injury, toxic exposures, intellectual property, and real estate.</p>
  <p style="top:340px">Our Kona office also offers commercial and hospitality litigation expertise on behalf of a wide variety of clients, including restaurants, hotels, property owners, and many others.</p>
  <div class="read-more"><span>READ MORE</span>
    <svg width="30" height="12" viewBox="0 0 30 12"><path d="M0 6H28M22 1l6 5-6 5" fill="none" stroke="#222" stroke-width="1.5"/></svg>
  </div>
</section>
<div class="abs label about-label">About Us</div>

<div class="abs city" role="img" aria-label="Monochrome upward view of tall city skyscrapers"></div>

<div class="abs label practice-label">Areas of Practice</div>
<section class="abs practice">
  <div class="row" style="height:167px"><h3>Family &amp; Divorce</h3><p>Our lawyers handle all aspects of family law on the Big Island and neighboring islands. We have more than 70 years of combined experience handling divorce, custody, and all aspects of family law.</p></div>
  <div class="row" style="height:176px"><h3>Personal Injury</h3><p>Dealing with personal injury and wrongful death claims is hard enough, so the lawyers of MCLG are here to make things as easy on you as possible. From Kailua Kona to Hilo, Hawaii to California, our attorneys are here for you.</p></div>
  <div class="row" style="height:178px"><h3>Corporate &amp; IP</h3><p>The attorneys at MCLG have been helping Big Island business owners with all their legal needs, so they can stay focused on what matters. Our lawyers have handled all aspects of business legal affairs for restaurants, hotels, car dealerships, medical practices, and more.</p></div>
  <div class="row last" style="height:166px"><h3>Real Estate</h3><p>Our lawyers work with home owners, buyers and property developers to ensure timely handling of all legal aspects involved in real estate.</p></div>
</section>

<section class="abs testimonials">
  <div class="label">Testimonials</div>
  <blockquote class="quote">" Lorem ipsum dolor sit amet, consectetur adipiscing elit, sed do eiusmod tempor incididunt ut labore et dolore magna aliqua. Ut enim ad minim veniam, quis nostrud exercitation ullamco laboris nisi ut aliquip ex ea commodo consequat. "</blockquote>
  <div class="cite">- Name Surname</div>
  <svg class="dots" width="60" height="14" viewBox="0 0 60 14">
    <circle cx="9" cy="7" r="5" fill="#fff"/>
    <circle cx="30" cy="7" r="4.5" fill="none" stroke="#fff" stroke-width="1.2"/>
    <circle cx="51" cy="7" r="4.5" fill="none" stroke="#fff" stroke-width="1.2"/>
  </svg>
</section>

<div class="abs label contact-label">Contact Us</div>
<section class="abs contact-box">
  <div class="col" style="width:343px">
    <h3>CONTACT</h3>
    <p>PHONE : +1.808.555.0148</p>
    <p>EMAIL : clients@tarnadvocate.example</p>
  </div>
  <div class="col" style="width:360px">
    <h3>LOCATION</h3>
    <p class="tight">48-2210 Halewai Road, Suite 310</p>
    <p class="tight">Kailua Kona, Hawaii 96740.</p>
  </div>
  <div class="col" style="width:343px">
    <h3>SITEMAP</h3>
    <p>Things to Do Before Filing for Divorce</p>
    <p>Things to Do During Custody Battle</p>
  </div>
</section>

<footer class="abs footer">©Meridian Crest Legal Group - 2019. All Rights Reserved.</footer>
</body>
</html>
```